Website Design - TallyPorchHelpers.net

PLEASE CHECK WORD DOCUMENT ATTACHED FOR WEBSITE FLOW.

Target Market(s)

REAL ESTATE AGENTS ARE THE TARGET MARKET

Industry/Entity Type

Real Estate

Coding

Coded - Design and coding required

Number of Pages Required

4 page

Colors

Designer to choose colors to be used in the design.

Requirements
Must have
• WE LIKE RED LOGO ATTACHED
Nice to have
• PLEASE CHECK WORD DOCUMENT ATTACHED FOR WEBSITE FLOW.
Should not have

```html
<!DOCTYPE html>
<html lang="en">
<head>
<meta charset="utf-8">
<title>TallyPorchHelpers.net — Open House Marketing for Agents</title>
<link href="https://fonts.googleapis.com/css2?family=Poppins:wght@400;500;600;700&family=Dancing+Script:wght@600&display=swap" rel="stylesheet">
<style>
:root{
  --red:#e41b23;
  --red-dark:#c4121a;
  --navy:#262c8c;
  --navy-deep:#1b2178;
  --plum:#8a2a6f;
  --ink:#2a2a35;
  --muted:#6d6f7b;
  --line:#e3e4ea;
  --paper:#f4f4f6;
  --white:#ffffff;
}
*{box-sizing:border-box;margin:0;padding:0}
html,body{width:1200px;height:4167px;overflow:hidden}
body{font-family:"Poppins",sans-serif;color:var(--ink);background:var(--white);font-size:12px;line-height:1.5}
.wrap{width:730px;margin:0 auto;position:relative}
.section-title{font-weight:700;font-size:22px;text-align:center}

/* header */
.site-header{height:83px;background:var(--white)}
.site-header .wrap{display:flex;align-items:center;height:83px;justify-content:space-between}
.brand{display:flex;align-items:center;gap:7px;font-weight:700;font-size:12px;color:var(--red);white-space:nowrap;flex:none}
.brand-box{width:24px;height:24px;background:var(--red);flex:none}
.main-nav{display:flex;gap:20px;font-size:9.5px;font-weight:500;letter-spacing:.4px;align-items:center;white-space:nowrap;flex:none}
.call{display:flex;align-items:center;gap:7px;white-space:nowrap;flex:none}
.call small{display:block;font-size:9px;color:var(--muted);line-height:1.2}
.call strong{display:block;font-size:12px;color:var(--red);line-height:1.2}

/* hero */
.hero{height:515px;position:relative;background:linear-gradient(180deg,#6b4a3c 0%,#8a6a56 45%,#4a3a36 100%)}
.hero-copy{position:absolute;left:0;right:0;top:190px;text-align:center;color:var(--white)}
.hero-copy h1{font-size:34px;font-weight:700;text-shadow:0 2px 8px rgba(0,0,0,.35)}
.hero-copy p{font-size:17px;line-height:1.35;text-shadow:0 2px 6px rgba(0,0,0,.35)}

/* options */
.options{height:236px;background:var(--red);color:var(--white)}
.options .section-title{padding-top:36px;font-size:21px}
.option-cards{display:flex;gap:20px;justify-content:center;margin-top:30px}
.option-card{width:230px;height:112px;background:var(--white);color:var(--ink);border-radius:4px;border-bottom:5px solid var(--red-dark);box-shadow:0 6px 14px rgba(0,0,0,.2);text-align:center;padding-top:20px;font-size:11px;font-weight:700;line-height:1.3}
.option-card span{display:block;font-weight:500}
.option-card svg{margin-bottom:8px}

/* how it works */
.how{height:333px;background:var(--paper)}
.how .section-title{padding-top:70px}
.steps{display:flex;justify-content:space-between;margin-top:50px;position:relative}
.step{width:200px;text-align:center;font-size:10px;color:var(--ink)}
.step-num{width:42px;height:42px;border-radius:50%;background:var(--navy);color:var(--white);font-weight:600;font-size:11px;display:flex;align-items:center;justify-content:center;margin:0 auto 16px;box-shadow:0 0 0 5px rgba(38,44,140,.15)}
.step-arrow{position:absolute;top:14px}

/* service area */
.service{height:161px;background:linear-gradient(90deg,var(--plum),var(--navy));color:var(--white);text-align:center}
.service .section-title{padding-top:34px}
.zip-form{display:flex;justify-content:center;margin-top:18px}
.zip-form .field{width:370px;height:34px;background:var(--white);color:#9a9ca6;font-size:10px;text-align:left;padding:9px 12px}
.btn{display:inline-flex;align-items:center;justify-content:center;font-weight:600;font-size:10px;color:var(--white);background:var(--red);letter-spacing:.5px}
.zip-form .btn{width:78px;height:34px}
.map{height:422px;background:linear-gradient(100deg,#a9cfe6 0%,#bcdcec 18%,#e8e6dc 30%,#efece2 60%,#e2e4d6 100%)}

/* marketing */
.marketing{height:530px;position:relative;background:linear-gradient(100deg,var(--navy) 0%,#4a2c86 55%,var(--plum) 100%);color:var(--white)}
.marketing .photo{position:absolute;right:0;top:0;width:460px;height:530px;background:linear-gradient(90deg,rgba(138,42,111,0) 0%,#b06a7a 45%,#c98a86 100%)}
.marketing .wrap{padding-top:52px}
.marketing h2{font-size:22px;font-weight:700;margin-bottom:34px}
.services{display:grid;grid-template-columns:240px 240px;column-gap:30px;row-gap:30px;width:510px}
.service-item h3{display:flex;align-items:center;gap:10px;font-size:13px;font-weight:600;margin-bottom:8px}
.service-item p{font-size:9.5px;line-height:1.6;opacity:.9}

/* packages */
.packages{height:610px;background:var(--paper)}
.packages .section-title{padding-top:60px}
.plans{display:flex;gap:22px;justify-content:center;margin-top:40px;align-items:flex-start}
.plan{width:128px;height:470px;background:var(--white);box-shadow:0 4px 14px rgba(0,0,0,.1);text-align:center;padding:16px 10px 0}
.plan.featured{margin-top:-12px;height:482px;border-top:30px solid var(--red);padding-top:0}
.plan h3{font-size:12px;font-weight:600;height:30px}
.plan.featured h3{margin-top:-24px;color:var(--white);height:34px}
.price{width:58px;height:58px;border-radius:50%;background:var(--red);color:var(--white);margin:0 auto 18px;display:flex;align-items:center;justify-content:center;font-weight:700;font-size:17px;box-shadow:0 0 0 5px rgba(228,27,35,.15)}
.price.navy{background:var(--navy);box-shadow:0 0 0 5px rgba(38,44,140,.15)}
.price sup{font-size:10px;margin-top:-8px}
.plan ul{list-style:none;text-align:left;font-size:9px;line-height:1.45}
.plan li{display:flex;gap:5px;margin-bottom:12px}
.plan li svg{flex:none;margin-top:2px}
.plan .btn{width:100px;height:34px;margin:16px auto 12px;background:var(--navy);font-size:9px}
.plan.featured .btn{background:var(--red)}
.plan .fine{font-size:8px;color:var(--muted);line-height:1.4}

/* faq */
.faq{height:430px;background:linear-gradient(180deg,var(--plum),var(--navy));color:var(--white)}
.faq .section-title{padding-top:52px;margin-bottom:34px}
.faq-cols{display:flex;gap:28px}
.faq-col{flex:1}
.faq-item{background:var(--white);color:var(--ink);font-size:10px;height:30px;padding:0 12px;display:flex;align-items:center;justify-content:space-between;margin-bottom:12px}
.faq-item b{font-weight:400;font-size:14px}
.faq-item.open{background:var(--red);color:var(--white);margin-bottom:0}
.faq-answer{background:var(--white);color:var(--muted);font-size:9.5px;padding:10px 12px;line-height:1.55;margin-bottom:12px}

/* testimonials */
.testimonials{height:515px;background:var(--paper)}
.testimonials .section-title{padding-top:62px;margin-bottom:38px}
.quotes{display:flex;gap:30px}
.quote{flex:1;text-align:center}
.quote-box{position:relative;background:var(--white);padding:18px 36px;font-size:10px;color:var(--muted);line-height:1.6}
.qmark{position:absolute;color:var(--red);font-size:34px;font-weight:700;line-height:1}
.qmark.open{left:10px;top:10px}
.qmark.close{right:10px;bottom:-6px}
.avatar{width:50px;height:50px;border-radius:50%;background:#d9d9de;border:3px solid var(--white);margin:18px auto 6px;box-shadow:0 2px 6px rgba(0,0,0,.15)}
.signature{font-family:"Dancing Script",cursive;font-size:22px;color:var(--ink)}
.dots{display:flex;gap:6px;justify-content:center;margin-top:30px}
.dots i{width:8px;height:8px;border-radius:50%;background:#d3d4da}
.dots i.on{background:var(--red)}

/* footer */
.site-footer{height:300px;background:var(--navy);color:var(--white);position:relative}
.newsletter{position:absolute;left:50%;top:-24px;transform:translateX(-50%);width:330px;height:46px;border-radius:23px;background:var(--red);display:flex;align-items:center;justify-content:center;gap:10px;font-weight:600;font-size:12px;letter-spacing:.5px;white-space:nowrap}
.footer-cols{display:flex;gap:24px;padding-top:50px}
.footer-col h4{font-size:10px;font-weight:600;margin-bottom:10px;letter-spacing:.3px}
.footer-col p,.footer-col li{font-size:9px;line-height:1.6;opacity:.9;list-style:none}
.col-about{width:180px}.col-contact{width:170px}.col-links{width:130px}.col-form{width:162px}
.socials{display:flex;gap:6px;margin-top:12px}
.socials i{width:18px;height:18px;border:1px solid rgba(255,255,255,.8);border-radius:50%}
.input{height:20px;background:var(--white);color:#9a9ca6;font-size:8px;padding:4px 6px;margin-bottom:6px}
.input.tall{height:46px}
.col-form .btn{width:100%;height:24px;font-size:8px}
.footer-bar{height:32px;background:var(--navy-deep);color:rgba(255,255,255,.8);font-size:8.5px}
.footer-bar .wrap{display:flex;justify-content:space-between;align-items:center;height:32px}
</style>
</head>
<body>

<header class="site-header">
  <div class="wrap">
    <div class="brand"><span class="brand-box"></span>TallyPorchHelpers.net</div>
    <nav class="main-nav">
      <span>HOW IT WORKS</span><span>SERVICE AREA</span><span>PRICING</span><span>ABOUT US</span><span>FAQ</span>
      <svg width="11" height="11" viewBox="0 0 12 12" fill="none" stroke="#2a2a35" stroke-width="1.6"><circle cx="5" cy="5" r="3.8"/><path d="M8 8l3 3"/></svg>
    </nav>
    <div class="call">
      <svg width="20" height="20" viewBox="0 0 24 24" fill="none" stroke="#e41b23" stroke-width="1.8"><path d="M5 3h4l2 5-2.5 1.5a11 11 0 005 5L15 12l5 2v4a2 2 0 01-2 2A16 16 0 013 5a2 2 0 012-2z"/></svg>
      <div><small>Call Or Text Us</small><strong>1-555-014-2290</strong></div>
    </div>
  </div>
</header>

<section class="hero" role="img" aria-label="Photo of a smiling couple being welcomed into a home by a real estate agent at an open house">
  <div class="hero-copy">
    <h1>Helping agents save time and money.</h1>
    <p>We place signs and boost foot traffic to your open houses<br>using proven marketing techniques.</p>
  </div>
</section>

<section class="options">
  <h2 class="section-title">Choose The Option Below That Best Describes You</h2>
  <div class="option-cards">
    <div class="option-card">
      <svg width="24" height="24" viewBox="0 0 24 24" fill="#e41b23"><path d="M3 21V7l6-3v17zm8 0V3h10v18zM13 6h2v2h-2zm4 0h2v2h-2zm-4 4h2v2h-2zm4 0h2v2h-2zm-4 4h2v2h-2zm4 0h2v2h-2z"/></svg>
      <span>I'M A</span>FULL ON BROKERAGE
    </div>
    <div class="option-card">
      <svg width="26" height="24" viewBox="0 0 26 24" fill="#e41b23"><circle cx="13" cy="7" r="4"/><circle cx="5" cy="9" r="3"/><circle cx="21" cy="9" r="3"/><path d="M6 21a7 7 0 0114 0zM0 20a5 5 0 017-4.5A8 8 0 005 20zm26 0a5 5 0 00-7-4.5 8 8 0 012 4.5z"/></svg>
      <span>I'M AN</span>IND. BROKER WITH A TEAM
    </div>
    <div class="option-card">
      <svg width="24" height="24" viewBox="0 0 24 24" fill="none" stroke="#e41b23" stroke-width="2"><path d="M5 22V3h15"/><rect x="9" y="7" width="11" height="8" fill="#e41b23"/></svg>
      <span>I NEED</span>SIGN PLACEMENT ASAP
    </div>
  </div>
</section>

<section class="how">
  <div class="wrap">
    <h2 class="section-title">How It Works</h2>
    <div class="steps">
      <div class="step"><div class="step-num">01</div>We boost Foot Traffic To Your Open House Using Proven Marketing Channels, Social Media Ads, SMS Notifications, Voice Broadcasts and Email Notifications</div>
      <svg class="step-arrow" style="left:205px" width="60" height="12" viewBox="0 0 60 12" fill="none" stroke="#2a2a35" stroke-width="1.2"><path d="M0 6h58M52 1l6 5-6 5"/></svg>
      <div class="step"><div class="step-num">02</div>We Place Open House Signs Strategically In The Surrounding Area</div>
      <svg class="step-arrow" style="left:465px" width="60" height="12" viewBox="0 0 60 12" fill="none" stroke="#2a2a35" stroke-width="1.2"><path d="M0 6h58M52 1l6 5-6 5"/></svg>
      <div class="step"><div class="step-num">03</div>Store custom signs for you if needed</div>
    </div>
  </div>
</section>

<section class="service">
  <h2 class="section-title">Service Area</h2>
  <div class="zip-form"><div class="field">Enter Your Open House Address</div><span class="btn">SUBMIT</span></div>
</section>
<div class="map" role="img" aria-label="Road map of the coastal service area showing cities, highways and the ocean"></div>

<section class="marketing">
  <div class="photo" role="img" aria-label="Photo of an excited woman shouting into a megaphone"></div>
  <div class="wrap">
    <h2>Marketing Services</h2>
    <div class="services">
      <div class="service-item">
        <h3><svg width="24" height="24" viewBox="0 0 24 24" fill="none" stroke="#fff" stroke-width="1.6"><path d="M4 5h16v11H9l-5 4z"/></svg>SMS</h3>
        <p>We will send a Text Message to all the people that live in the surrounding area of your Open House to let them know there is a home for sale in their neighborhood and to let anyone that they may know looking to purchase a new home to come check it out!</p>
      </div>
      <div class="service-item">
        <h3><svg width="24" height="24" viewBox="0 0 24 24" fill="none" stroke="#fff" stroke-width="1.6"><rect x="3" y="6" width="18" height="12"/><path d="M3 6l9 7 9-7"/></svg>EMAIL</h3>
        <p>We will send an Email Message to all the people that live in the surrounding area of your Open House to let them know there is a home for sale in their neighborhood and to let anyone that they may know looking to purchase a new home to come check it out!</p>
      </div>
      <div class="service-item">
        <h3><svg width="24" height="24" viewBox="0 0 24 24" fill="none" stroke="#fff" stroke-width="1.6"><rect x="3" y="4" width="18" height="12"/><path d="M9 20h6M12 16v4"/></svg>SOCIAL MEDIA ADS</h3>
        <p>We will place a Social Media Ad in the home feeds of all the people that live in the surrounding area of your Open House to let them know there is a home for sale in their neighborhood and to let anyone that they may know looking to purchase a new home to come check it out!</p>
      </div>
      <div class="service-item">
        <h3><svg width="24" height="24" viewBox="0 0 24 24" fill="none" stroke="#fff" stroke-width="1.6"><rect x="9" y="3" width="6" height="11" rx="3"/><path d="M6 11a6 6 0 0012 0M12 17v4M9 21h6"/></svg>VOICE BROADCAST</h3>
        <p>We will send a voice broadcast to all the people that live in the surrounding area of your Open House to let them know there is a home for sale in their neighborhood and to let anyone that they may know looking to purchase a new home to come check it out!</p>
      </div>
    </div>
  </div>
</section>

<section class="packages">
  <h2 class="section-title">Choose Your Package</h2>
  <div class="plans">
    <div class="plan">
      <h3>5 SIGNS</h3><div class="price"><sup>$</sup>49</div>
      <ul>
        <li><svg width="9" height="9" viewBox="0 0 10 10" fill="none" stroke="#262c8c" stroke-width="2"><path d="M1 5l3 3 5-7"/></svg>Place signs strategically in best areas according to where the open house is located</li>
        <li><svg width="9" height="9" viewBox="0 0 10 10" fill="none" stroke="#262c8c" stroke-width="2"><path d="M1 5l3 3 5-7"/></svg>Pick up the signs after the open house</li>
        <li><svg width="9" height="9" viewBox="0 0 10 10" fill="none" stroke="#262c8c" stroke-width="2"><path d="M1 5l3 3 5-7"/></svg>Store custom signs for you if needed</li>
      </ul>
      <span class="btn">SIGN UP</span>
      <p class="fine">Sign Up For A Subscription And Get These Marketing Services For Free.</p>
    </div>
    <div class="plan">
      <h3>10 SIGNS</h3><div class="price"><sup>$</sup>59</div>
      <ul>
        <li><svg width="9" height="9" viewBox="0 0 10 10" fill="none" stroke="#262c8c" stroke-width="2"><path d="M1 5l3 3 5-7"/></svg>Place signs strategically in best areas according to where the open house is located</li>
        <li><svg width="9" height="9" viewBox="0 0 10 10" fill="none" stroke="#262c8c" stroke-width="2"><path d="M1 5l3 3 5-7"/></svg>Pick up the signs after the open house</li>
        <li><svg width="9" height="9" viewBox="0 0 10 10" fill="none" stroke="#262c8c" stroke-width="2"><path d="M1 5l3 3 5-7"/></svg>Store custom signs for you if needed</li>
      </ul>
      <span class="btn">SIGN UP</span>
      <p class="fine">Sign Up For A Subscription And Get These Marketing Services For Free.</p>
    </div>
    <div class="plan featured">
      <h3>15 SIGNS</h3><div class="price navy"><sup>$</sup>69</div>
      <ul>
        <li><svg width="9" height="9" viewBox="0 0 10 10" fill="none" stroke="#262c8c" stroke-width="2"><path d="M1 5l3 3 5-7"/></svg>Place signs strategically in best areas according to where the open house is located</li>
        <li><svg width="9" height="9" viewBox="0 0 10 10" fill="none" stroke="#262c8c" stroke-width="2"><path d="M1 5l3 3 5-7"/></svg>Pick up the signs after the open house</li>
        <li><svg width="9" height="9" viewBox="0 0 10 10" fill="none" stroke="#262c8c" stroke-width="2"><path d="M1 5l3 3 5-7"/></svg>Store custom signs for you if needed</li>
      </ul>
      <span class="btn">SIGN UP</span>
      <p class="fine">Sign Up For A Subscription And Get These Marketing Services For Free.</p>
    </div>
    <div class="plan">
      <h3>20 SIGNS</h3><div class="price"><sup>$</sup>79</div>
      <ul>
        <li><svg width="9" height="9" viewBox="0 0 10 10" fill="none" stroke="#262c8c" stroke-width="2"><path d="M1 5l3 3 5-7"/></svg>Place signs strategically in best areas according to where the open house is located</li>
        <li><svg width="9" height="9" viewBox="0 0 10 10" fill="none" stroke="#262c8c" stroke-width="2"><path d="M1 5l3 3 5-7"/></svg>Pick up the signs after the open house</li>
        <li><svg width="9" height="9" viewBox="0 0 10 10" fill="none" stroke="#262c8c" stroke-width="2"><path d="M1 5l3 3 5-7"/></svg>Store custom signs for you if needed</li>
      </ul>
      <span class="btn">SIGN UP</span>
      <p class="fine">Sign Up For A Subscription And Get These Marketing Services For Free.</p>
    </div>
    <div class="plan">
      <h3>25+ SIGNS</h3><div style="height:76px"></div>
      <ul>
        <li><svg width="9" height="9" viewBox="0 0 10 10" fill="none" stroke="#262c8c" stroke-width="2"><path d="M1 5l3 3 5-7"/></svg>Place signs strategically in best areas according to where the open house is located</li>
        <li><svg width="9" height="9" viewBox="0 0 10 10" fill="none" stroke="#262c8c" stroke-width="2"><path d="M1 5l3 3 5-7"/></svg>Pick up the signs after the open house</li>
        <li><svg width="9" height="9" viewBox="0 0 10 10" fill="none" stroke="#262c8c" stroke-width="2"><path d="M1 5l3 3 5-7"/></svg>Store custom signs for you if needed</li>
      </ul>
      <span class="btn" style="font-size:7.5px;line-height:1.2;text-align:center">CLICK BUTTON TO<br>CREATE CUSTOM PKG</span>
      <p class="fine">Sign Up For A Subscription And Get These Marketing Services For Free.</p>
    </div>
  </div>
</section>

<section class="faq">
  <div class="wrap">
    <h2 class="section-title">Frequently Asked Questions</h2>
    <div class="faq-cols">
      <div class="faq-col">
        <div class="faq-item">Vestibulum sed felis a ante suscipit auctor<b>+</b></div>
        <div class="faq-item">Sed ullamcorper augue ut facilisis condimentum<b>+</b></div>
        <div class="faq-item">Curabitur at ligula sed velit feugiat pellentesque<b>+</b></div>
        <div class="faq-item">Nam vitae velit non augue ultricies laoreet<b>+</b></div>
      </div>
      <div class="faq-col">
        <div class="faq-item">Curabitur at ligula sed velit feugiat pellentesque<b>+</b></div>
        <div class="faq-item open">Lorem ipsum used in various languages for layouts<b>&minus;</b></div>
        <div class="faq-answer">In publishing and graphic design, lorem ipsum is a placeholder text commonly used to demonstrate the visual. In publishing graphic design, lorem ipsum is a placeholder text commonly used to demonstrate the visual form of a document.</div>
        <div class="faq-item">Sed ullamcorper augue ut facilisis condimentum<b>+</b></div>
        <div class="faq-item">Nam vitae velit non augue ultricies laoreet<b>+</b></div>
      </div>
    </div>
  </div>
</section>

<section class="testimonials">
  <div class="wrap">
    <h2 class="section-title">Clients Testimonials</h2>
    <div class="quotes">
      <div class="quote">
        <div class="quote-box"><span class="qmark open">&ldquo;</span>In publishing and graphic design, lorem ipsum is a placeholder text commonly used to demonstrate the visual. In publishing graphic design, lorem ipsum is a placeholder text commonly used to demonstrate the visual form of a document. Demonstrate the visual. In publishing graphic design, lorem ipsum is a text commonly used to demonstrate the visual form of a document.<span class="qmark close">&rdquo;</span></div>
        <div class="avatar" role="img" aria-label="Client portrait"></div>
        <div class="signature">Marisol Avery</div>
      </div>
      <div class="quote">
        <div class="quote-box"><span class="qmark open">&ldquo;</span>In publishing and graphic design, lorem ipsum is a placeholder text commonly used to demonstrate the visual. In publishing graphic design, lorem ipsum is a placeholder text commonly used to demonstrate the visual form of a document. Demonstrate the visual. In publishing graphic design, lorem ipsum is a text commonly used to demonstrate the visual form of a document.<span class="qmark close">&rdquo;</span></div>
        <div class="avatar" role="img" aria-label="Client portrait"></div>
        <div class="signature">Dexter Holloway</div>
      </div>
    </div>
    <div class="dots"><i></i><i></i><i class="on"></i><i></i><i></i></div>
  </div>
</section>

<footer class="site-footer">
  <div class="newsletter">
    <svg width="18" height="14" viewBox="0 0 18 14" fill="none" stroke="#fff" stroke-width="1.5"><path d="M1 7l16-6-4 12-4-4z M9 9l-2 4"/></svg>
    SUBSCRIBE TO OUR NEWSLETTER
  </div>
  <div class="wrap">
    <div class="footer-cols">
      <div class="footer-col col-about">
        <h4>ABOUT TALLY PORCH HELPERS</h4>
        <p>Owned and operated by a highly experienced Premier Realtor and a top Realtor, we help agents leverage their time and skills to increase production at an affordable price with impeccable support.</p>
        <div class="socials"><i></i><i></i><i></i><i></i><i></i></div>
      </div>
      <div class="footer-col col-contact">
        <h4>CONTACT INFORMATION</h4>
        <p>4410 Maple Crest Avenue,<br>Suite 210, Arden, TX 75000</p>
        <p style="margin-top:8px">1-555-014-2290</p>
        <p>info@tallyporchhelpers.net</p>
      </div>
      <div class="footer-col col-links">
        <h4>QUICK LINKS</h4>
        <ul><li>How it Works</li><li>Service Area</li><li>Pricing</li><li>About Us</li><li>FAQ</li></ul>
      </div>
      <div class="footer-col col-form">
        <h4>CONTACT US RIGHT NOW</h4>
        <div class="input">Name</div>
        <div class="input">Email</div>
        <div class="input">Phone</div>
        <div class="input tall">Message</div>
        <span class="btn">SEND A MESSAGE</span>
      </div>
    </div>
  </div>
</footer>
<div class="footer-bar">
  <div class="wrap"><span>Copyright &copy; 2018 TallyPorchHelpers.net</span><span>Terms of Use | Privacy | Sitemap</span></div>
</div>

</body>
</html>
```